Facebook Post for Fence Spring Sale

We have a $12 / FT Fence sale that we have been running for a while now. We need a flyer made up for SPRING.

Our previous flyer can be seen here:
https://media-cdn4.pixvaultcloud.example/img/v2/58120947_302918475610234_1937465028364719205_n.jpg?k=7c2e91b04d3a58f6e2b7c1d9a0f46e83&t=72A19C04

We want to use the photos that are shown here https://files.boxmeadow.example/share?id=7QxLm2pRtKwZs9VnHyBcJdEf4Ga in the flyer. This is to be posted on Facebook so it must be the proper size for Facebook page post.

The wording to be used should be "Spring Fence Sale" and "$12 / FT Wood Fences" Also we should include our business name "Oakvale Fence" and phone number for Free Estimates - 555-216-4073.

Industry/Entity Type

Residential Construction

Font styles to use
Serif
Sans Serif

Colors
3176b5
fbee3d
fbed22
fbf289
85cae6
33a6d7

Requirements
Must have
• Phone number, $12 / FT Fence Sale

```html
<!DOCTYPE html>
<html lang="en">
<head>
<meta charset="utf-8">
<title>Oakvale Fence – Spring Fence Sale</title>
<link rel="stylesheet" href="https://fonts.googleapis.com/css2?family=Roboto+Condensed:ital,wght@0,700;1,800&family=Arimo:wght@700&display=swap">
<style>
  :root {
    --lime: #a9cf2f;
    --lime-light: #cfe65a;
    --lime-pale: #eef7a4;
    --forest: #0f5a25;
    --phone-yellow: #fbed22;
    --ink: #2a2a10;
    --white: #ffffff;
    --grass: #6f9a3c;
    --wood: #d9b97a;
    --wood-dark: #b98a4a;
  }
  html, body {
    margin: 0;
    padding: 0;
    width: 1200px;
    height: 1200px;
    overflow: hidden;
    background: var(--white);
  }
  .flyer {
    position: absolute;
    left: 146px;
    top: 148px;
    width: 892px;
    height: 902px;
    overflow: hidden;
    background: linear-gradient(180deg, var(--lime) 0%, var(--lime-light) 40%, var(--lime-pale) 52%, var(--lime) 100%);
    box-shadow: 0 10px 40px rgba(0,0,0,0.35);
    font-family: "Roboto Condensed", sans-serif;
  }
  .headline {
    position: absolute;
    left: 0;
    width: 100%;
    margin: 0;
    text-align: center;
    font-style: italic;
    font-weight: 800;
    line-height: 1;
    white-space: nowrap;
  }
  .headline--brand {
    top: 16px;
    left: 20px;
    font-size: 114px;
    color: var(--white);
    text-shadow: 2px 3px 0 #5a5a5a, 4px 6px 6px rgba(0,0,0,0.35);
  }
  .headline--sale {
    top: 128px;
    font-size: 118px;
    color: var(--forest);
    text-shadow: 2px 3px 0 #083816, 4px 6px 6px rgba(0,0,0,0.3);
  }
  .gallery {
    position: absolute;
    top: 252px;
    left: 16px;
    display: flex;
    gap: 18px;
  }
  .gallery__photo {
    width: 203px;
    height: 203px;
    border-radius: 10px;
  }
  .gallery__photo--gate { background: linear-gradient(180deg, #4f7a33 0%, #d8cc95 50%, #6a9a3a 100%); }
  .gallery__photo--scallop { background: linear-gradient(90deg, #b98a4a 0%, #d9b97a 60%, #7ea048 100%); }
  .gallery__photo--picket { background: linear-gradient(180deg, #8a7f6a 0%, #e6dccb 40%, #c9b89e 100%); }
  .gallery__photo--privacy { background: linear-gradient(90deg, #d9a35a 0%, #e7bb78 60%, #c98f48 100%); }
  .hero {
    position: absolute;
    left: 0;
    top: 477px;
    width: 892px;
    height: 404px;
    background: linear-gradient(180deg, #7fae45 0%, var(--grass) 30%, var(--wood) 55%, var(--wood-dark) 100%);
  }
  .offer {
    position: absolute;
    right: 48px;
    top: 486px;
    margin: 0;
    line-height: 1;
    font-family: "Arimo", sans-serif;
    font-weight: 700;
    font-size: 74px;
    letter-spacing: 1px;
    color: var(--white);
    text-shadow: 2px 3px 4px rgba(0,0,0,0.55);
    white-space: nowrap;
  }
  .estimates {
    position: absolute;
    right: 50px;
    top: 588px;
    margin: 0;
    line-height: 1;
    font-weight: 700;
    font-size: 74px;
    color: var(--white);
    text-shadow: 2px 3px 4px rgba(0,0,0,0.55);
    white-space: nowrap;
  }
  .contact {
    position: absolute;
    left: 64px;
    top: 680px;
    display: flex;
    align-items: center;
    gap: 26px;
  }
  .contact__icon { width: 100px; height: 100px; }
  .contact__number {
    font-family: "Arimo", sans-serif;
    font-weight: 700;
    font-size: 104px;
    line-height: 1;
    color: var(--phone-yellow);
    -webkit-text-stroke: 2px var(--ink);
    text-shadow: 3px 4px 4px rgba(0,0,0,0.5);
    white-space: nowrap;
  }
  .web-band {
    position: absolute;
    left: 0;
    top: 823px;
    width: 892px;
    height: 56px;
    background: rgba(30, 100, 40, 0.88);
    color: var(--white);
    font-family: "Arimo", sans-serif;
    font-weight: 700;
    font-size: 38px;
    line-height: 56px;
    text-align: center;
  }
  .base-strip {
    position: absolute;
    left: 0;
    top: 879px;
    width: 892px;
    height: 23px;
    background: linear-gradient(90deg, var(--lime) 0%, var(--lime-pale) 50%, var(--lime) 100%);
  }
</style>
</head>
<body>
  <main class="flyer">
    <h1 class="headline headline--brand">Oakvale Fence</h1>
    <h2 class="headline headline--sale">Spring Fence Sale</h2>

    <div class="gallery">
      <div class="gallery__photo gallery__photo--gate" role="img" aria-label="Photo of an arched wooden picket gate set in a split-rail fence on a lawn"></div>
      <div class="gallery__photo gallery__photo--scallop" role="img" aria-label="Photo of a scalloped wooden privacy fence running along a yard"></div>
      <div class="gallery__photo gallery__photo--picket" role="img" aria-label="Photo of a pointed wooden picket gate with black hinges"></div>
      <div class="gallery__photo gallery__photo--privacy" role="img" aria-label="Photo of an arched wooden privacy fence with a company yard sign"></div>
    </div>

    <div class="hero" role="img" aria-label="Photo of a new wooden picket fence stretching across a green lawn"></div>

    <p class="offer">$12 / FT Wood Fences</p>
    <p class="estimates">Free Estimates</p>

    <div class="contact">
      <svg class="contact__icon" viewBox="0 0 100 100" aria-hidden="true">
        <circle cx="50" cy="50" r="44" fill="none" stroke="#fbed22" stroke-width="6"/>
        <circle cx="50" cy="50" r="44" fill="none" stroke="#2a2a10" stroke-width="1.5"/>
        <path d="M36 24 c-6 4 -10 10 -8 20 c3 14 14 28 26 34 c8 4 14 2 18 -4 l-10 -9 c-3 3 -6 3 -9 1 c-6 -5 -11 -12 -13 -19 c-1 -3 1 -5 4 -7 z" fill="#fbed22" stroke="#2a2a10" stroke-width="2"/>
      </svg>
      <span class="contact__number">555-216-4073</span>
    </div>

    <div class="web-band">www.MyOakvaleFence.com</div>
    <div class="base-strip"></div>
  </main>
</body>
</html>
```